Silver Bloom Marisol's Cleaning Service Business Cards Project

A business card with all contact details with logo design on there (already have a logo) eye catching Logo and contact info on one side, full logo on the back, must target upper class residential and corporate companies, fitness companies, still keep it on the feminine side of things , must look elegant

Target Market(s)

Upper class homes and corporate companies

Industry/Entity Type

Cleaning Service

Contact Information for Business Card

Name: Marisol Quenby
Position: Director
ABN: 31647209853
Email: marisolssilvercleaning@tidymail.example
Number: 0417906354

Font styles to use
Decorative

Colors

Designer to choose colors to be used in the design.

Requirements
Must have
• Available Sydney Wide, contact info and logo on one side, full logo on the back
Nice to have
• Professional appearance
Should not have
• Cheap advert looking stuff

```html
<!DOCTYPE html>
<html lang="en">
<head>
<meta charset="utf-8">
<title>Silver Bloom – Business Cards</title>
<link href="https://fonts.googleapis.com/css2?family=Roboto:wght@400;500&display=swap" rel="stylesheet">
<style>
  :root {
    --backdrop: #e9e5df;
    --front-bg: #1c1d1f;
    --back-bg: #2d313f;
    --accent: #3fe3d3;
    --text-light: #ffffff;
    --rule: #a9acb0;
  }
  * { margin: 0; padding: 0; box-sizing: border-box; }
  html, body {
    width: 1200px; height: 960px; overflow: hidden;
    background: var(--backdrop);
    font-family: "Roboto", Arial, sans-serif;
  }
  .canvas { position: relative; width: 1200px; height: 960px; }
  .card {
    position: absolute; width: 600px; height: 342px; overflow: hidden;
    box-shadow: 0 4px 10px rgba(0,0,0,0.25);
  }
  .card-front { left: 314px; top: 113px; background: var(--front-bg); }
  .card-back  { left: 311px; top: 473px; background: var(--back-bg); }

  .edge-tab {
    position: absolute; left: -14px; top: 187px;
    width: 28px; height: 28px; border-radius: 50%; background: var(--accent);
  }
  .brand {
    position: absolute; right: 40px; top: 140px; width: 200px;
    text-align: center; color: var(--accent);
    font-weight: 500; text-transform: uppercase;
  }
  .brand-name { font-size: 19px; letter-spacing: 1px; line-height: 1.2; }
  .brand-sub { font-size: 8px; letter-spacing: 1.6px; margin-top: 4px; }

  .person { position: absolute; left: 38px; top: 176px; color: var(--accent); }
  .person-name { font-size: 19px; font-weight: 500; letter-spacing: 0.2px; }
  .person-role { font-size: 14px; font-weight: 500; margin-top: 3px; }

  .divider {
    position: absolute; left: 34px; top: 238px; width: 524px;
    height: 1px; background: var(--rule);
  }
  .contacts { position: absolute; left: 38px; top: 262px; list-style: none; }
  .contacts li {
    display: flex; align-items: center; gap: 8px;
    color: var(--text-light); font-size: 14px; height: 19.5px;
  }
  .contacts svg { width: 12px; height: 12px; fill: var(--accent); flex: none; }
  .abn { position: absolute; right: 36px; top: 298px; color: var(--text-light); font-size: 14px; }

  .back-brand {
    position: absolute; left: 0; right: 0; top: 120px;
    text-align: center; color: var(--accent);
    font-weight: 500; text-transform: uppercase;
  }
  .back-brand .brand-name { font-size: 34px; letter-spacing: 3px; }
  .back-brand .brand-sub { font-size: 13px; letter-spacing: 3px; margin-top: 10px; }
  .back-web {
    position: absolute; left: 0; right: 0; top: 288px;
    text-align: center; color: var(--text-light);
    font-size: 14px; letter-spacing: 4.2px;
  }
</style>
</head>
<body>
<main class="canvas">
  <section class="card card-front" aria-label="Business card front">
    <span class="edge-tab"></span>
    <div class="brand">
      <div class="brand-name">Silver Bloom</div>
      <div class="brand-sub">Marisol's Cleaning Service</div>
    </div>
    <div class="person">
      <div class="person-name">MARISOL QUENBY</div>
      <div class="person-role">DIRECTOR</div>
    </div>
    <div class="divider"></div>
    <ul class="contacts">
      <li>
        <svg viewBox="0 0 24 24" aria-hidden="true"><path d="M6.6 10.8a15.1 15.1 0 0 0 6.6 6.6l2.2-2.2a1 1 0 0 1 1-.25 11.4 11.4 0 0 0 3.6.57 1 1 0 0 1 1 1V20a1 1 0 0 1-1 1A17 17 0 0 1 3 4a1 1 0 0 1 1-1h3.5a1 1 0 0 1 1 1c0 1.25.2 2.45.57 3.57a1 1 0 0 1-.25 1z"/></svg>
        0417906354
      </li>
      <li>
        <svg viewBox="0 0 24 24" aria-hidden="true"><path d="M2 5h20v2l-10 6L2 7z"/><path d="M2 9l10 6 10-6v10H2z"/></svg>
        marisolssilvercleaning@tidymail.example
      </li>
      <li>
        <svg viewBox="0 0 24 24" aria-hidden="true"><path d="M12 2a10 10 0 1 0 0 20 10 10 0 0 0 0-20zm-1 17.9A8 8 0 0 1 4.1 11H7v2l3 3v3.9zm6.9-2.5A2 2 0 0 0 16 16h-1v-3a1 1 0 0 0-1-1H8v-2h2a1 1 0 0 0 1-1V7h2a2 2 0 0 0 2-2v-.4a8 8 0 0 1 2.9 12.8z"/></svg>
        www.silverbloomclean.example
      </li>
    </ul>
    <div class="abn">ABN: 31647209853</div>
  </section>

  <section class="card card-back" aria-label="Business card back">
    <div class="back-brand">
      <div class="brand-name">Silver Bloom</div>
      <div class="brand-sub">Marisol's Cleaning Service</div>
    </div>
    <div class="back-web">www.silverbloomclean.example</div>
  </section>
</main>
</body>
</html>
```